For Sale Sign for Real Estate Agency

We need a For Sale Sign designed for our agency. I want a very simple/elegant sign that says "For Sale" towards the top of the sign (not in huge letters). Most of the sign should be a design/picture with our name and phone number somewhere at the bottom.

One significant detail, it's important that our logo not be too big or the center piece of the sign. Since our company name has the word "rent" in it, people assume the house is for rent, instead of for sale.

I attached our logo and a rough outline of the format I'm looking for.

Again, I'm looking for elegant and simple! Thanks for your time

Industry/Entity Type

Real Estate

Colors

Designer to choose colors to be used in the design.

Requirements
Must have
Nice to have
Should not have
• Nothing tacky!
• Our logo/company name should not be too big or the center piece of the sign. Since our company name has the word "rent" in it, people assume the house is for rent, instead of for sale.

```html
<!DOCTYPE html>
<html lang="en">
<head>
<meta charset="utf-8">
<title>For Sale Sign – HomeVest Realty</title>
<link href="https://fonts.googleapis.com/css2?family=Bebas+Neue&family=Source+Sans+3:wght@400&display=swap" rel="stylesheet">
<style>
  :root {
    --backdrop: #1e1e1e;
    --sign-white: #ffffff;
    --sale-red: #ec1f27;
    --ink: #231f20;
    --roof-grey: #545555;
    --wall-orange: #c66422;
  }
  * { margin: 0; padding: 0; box-sizing: border-box; }
  html, body {
    width: 1200px;
    height: 1000px;
    overflow: hidden;
    background: var(--backdrop);
  }
  .canvas {
    position: relative;
    width: 1200px;
    height: 1000px;
  }
  .sign {
    position: absolute;
    left: 264px;
    top: 52px;
    width: 671px;
    height: 895px;
    background: var(--sign-white);
  }
  .sale-band {
    position: absolute;
    left: 0;
    top: 46px;
    width: 100%;
    height: 175px;
    background: var(--sale-red);
    display: flex;
    align-items: center;
    justify-content: center;
  }
  .sale-band__title {
    font-family: "Bebas Neue", "Arial Narrow", sans-serif;
    font-weight: 400;
    font-size: 184px;
    line-height: 1;
    color: var(--sign-white);
    letter-spacing: 2px;
    padding-top: 14px;
  }
  .house-illustration {
    position: absolute;
    left: 88px;
    top: 252px;
    width: 496px;
    height: 391px;
    border-radius: 4px;
    background: linear-gradient(180deg, var(--roof-grey) 0%, var(--wall-orange) 100%);
  }
  .agency {
    position: absolute;
    left: 0;
    top: 678px;
    width: 100%;
    text-align: center;
  }
  .agency__name {
    display: inline-block;
    font-family: "Source Sans 3", "Helvetica Neue", sans-serif;
    font-weight: 400;
    color: var(--ink);
    font-size: 60px;
    line-height: 1;
    letter-spacing: -1.5px;
    text-align: right;
  }
  .agency__name-sub {
    display: block;
    font-size: 26px;
    letter-spacing: 4px;
    line-height: 1;
    margin-top: 0;
  }
  .agency__phone {
    display: block;
    margin-top: 14px;
    font-family: "Bebas Neue", "Arial Narrow", sans-serif;
    font-size: 66px;
    line-height: 1;
    color: var(--sale-red);
    letter-spacing: 1px;
  }
  .phone-rules {
    position: absolute;
    left: 188px;
    top: 830px;
  }
</style>
</head>
<body>
  <div class="canvas">
    <div class="sign">
      <div class="sale-band">
        <h1 class="sale-band__title">For Sale</h1>
      </div>

      <div class="house-illustration" role="img" aria-label="Flat illustration of an orange house with a grey gabled roof, chimney, white door, window and small picket fence on a strip of lawn"></div>

      <div class="agency">
        <p class="agency__name">HomeVest<span class="agency__name-sub">Realty</span></p>
        <span class="agency__phone">401.555.0148</span>
      </div>

      <svg class="phone-rules" width="300" height="30" viewBox="0 0 300 30" aria-hidden="true">
        <line x1="0" y1="3" x2="296" y2="3" stroke="var(--sale-red)" stroke-width="3"/>
        <line x1="22" y1="15" x2="273" y2="15" stroke="var(--sale-red)" stroke-width="2"/>
        <line x1="53" y1="27" x2="243" y2="27" stroke="var(--sale-red)" stroke-width="2"/>
      </svg>
    </div>
  </div>
</body>
</html>
```